Redesign Website - Current one too plain

The description is in the uploaded file. Please let me know if you need any more information. I'd prefer it if someone could implement the design to a WordPress site but the best design will win, regardless.
I would like the forms to look nice as well
UPDATE:
I don't think we can use the images that I provided, I think they make the site look a bit 'cheap' and I really don't know how to replace them. One thought I have had is to make the "Simple, Unique, Effective" a second feature on the right side of the page with the search on the left
Target Market(s)
Small companies, private sellers of cars and people who rent their caravan/holiday home out
Industry/Entity Type
Advertising
Number of Pages Required
3 page
Colors
Designer to choose colors to be used in the design.
Look and feel
Each slider illustrates characteristics of the customer's brand and the style your logo design should communicate.

```html
<!DOCTYPE html>
<html lang="en">
<head>
<meta charset="utf-8">
<title>Kodeo.com – Find adverts by code</title>
<link rel="stylesheet" href="https://fonts.googleapis.com/css2?family=Poppins:wght@400;500;600;700&family=Baloo+2:wght@500;600;700&display=swap">
<style>
  :root {
    --lime: #d4ec00;
    --lime-dark: #c3da00;
    --charcoal: #2b2b2b;
    --charcoal-soft: #333333;
    --navy: #14325c;
    --grey-bg: #f0f0f0;
    --text: #3a3a3a;
    --muted: #555555;
    --white: #ffffff;
    --star: #f0a020;
  }
  * { box-sizing: border-box; margin: 0; padding: 0; }
  html, body { width: 1200px; height: 2737px; overflow: hidden; }
  body { position: relative; font-family: "Poppins", sans-serif; color: var(--text); background: var(--white); }
  .abs { position: absolute; }

  /* Header */
  .site-header { left: 0; top: 0; width: 1200px; height: 73px; background: var(--charcoal); }
  .main-nav a { position: absolute; top: 30px; color: var(--white); font-size: 14px; text-decoration: none; }
  .brand { position: absolute; left: 512px; top: 28px; display: flex; align-items: center; gap: 9px; color: var(--lime); font-weight: 600; font-size: 21px; letter-spacing: 2px; }
  .brand-dot { width: 14px; height: 14px; border-radius: 50%; background: var(--lime); }
  .header-search { position: absolute; left: 905px; top: 30px; color: var(--white); font-size: 14px; }
  .login-btn { position: absolute; left: 1009px; top: 18px; width: 88px; height: 37px; background: var(--lime); color: var(--charcoal); font-size: 15px; font-weight: 500; display: flex; align-items: center; justify-content: center; }

  /* Hero */
  .hero { left: 0; top: 73px; width: 1200px; height: 601px; background: linear-gradient(100deg, var(--lime-dark) 0%, var(--lime) 60%); }
  .hero-visual { left: 21px; top: 186px; width: 729px; height: 372px; border-radius: 10px; background: linear-gradient(180deg, #c8c8c4 0%, #9a9a98 100%); opacity: .9; }
  .search-panel { left: 775px; top: 216px; width: 359px; height: 340px; border-radius: 18px; background: var(--charcoal); }
  .code-display { position: absolute; left: 0; width: 100%; top: 46px; text-align: center; color: var(--lime); font-size: 92px; font-weight: 500; line-height: 1; }
  .code-arrows { position: absolute; top: 52px; left: 0; width: 100%; height: 110px; }
  .category-tabs { position: absolute; left: 26px; top: 187px; width: 307px; height: 38px; display: flex; border: 2px solid var(--lime); }
  .category-tabs span { flex: 1; display: flex; align-items: center; justify-content: center; font-size: 16px; font-weight: 500; color: var(--lime); border-left: 2px solid var(--lime); }
  .category-tabs span:first-child { border-left: 0; background: var(--lime); color: var(--charcoal); }
  .search-btn { position: absolute; left: 116px; top: 246px; width: 128px; height: 38px; background: var(--lime); color: var(--charcoal); font-size: 16px; font-weight: 500; display: flex; align-items: center; justify-content: center; }

  /* Features */
  .feature-swoosh { left: 150px; top: 880px; }
  .feature-card { top: 762px; width: 257px; height: 226px; background: var(--white); border-radius: 12px; box-shadow: 0 4px 18px rgba(0,0,0,.09); text-align: center; }
  .feature-icon { position: absolute; left: 88px; top: 24px; width: 82px; height: 82px; }
  .feature-title { position: absolute; left: 0; width: 100%; top: 118px; font-family: "Baloo 2", sans-serif; font-weight: 600; font-size: 25px; color: var(--charcoal); }
  .feature-text { position: absolute; left: 22px; width: 213px; top: 162px; font-size: 12px; line-height: 18px; color: var(--muted); }

  /* About */
  .about { left: 0; top: 1060px; width: 1200px; height: 593px; background: var(--grey-bg); }
  .about-visual { left: 112px; top: 1105px; width: 432px; height: 502px; border-radius: 46% 40% 48% 38%; background: linear-gradient(135deg, #b9c2cc 0%, #6d7680 60%, #4d545b 100%); }
  .about-title { left: 639px; top: 1150px; font-size: 31px; font-weight: 700; color: var(--navy); }
  .about-copy { left: 639px; top: 1209px; width: 458px; font-size: 15px; line-height: 26.5px; color: var(--text); }
  .about-copy p + p { margin-top: 8px; }

  /* Testimonials */
  .testimonials-title { left: 0; width: 1200px; top: 1748px; text-align: center; font-size: 42px; font-weight: 700; color: var(--navy); }
  .testimonial { top: 1887px; width: 318px; height: 205px; background: var(--white); border: 1px solid #c9c9c9; border-top: 4px solid #8c8c8c; border-radius: 4px; }
  .testimonial.is-featured { border-color: var(--lime); border-top-color: var(--lime); }
  .testimonial p { position: absolute; left: 12px; width: 294px; top: 54px; text-align: center; font-size: 11.5px; line-height: 23px; color: var(--text); }
  .avatar { position: absolute; left: 114px; top: -48px; width: 90px; height: 90px; border-radius: 50%; border: 3px solid var(--white); box-shadow: 0 0 0 1px #c9c9c9; background: linear-gradient(160deg, #c9cfd6, #6c747c); }
  .is-featured .avatar { box-shadow: 0 0 0 1px var(--lime); }
  .pointer { position: absolute; left: 140px; bottom: -36px; }
  .reviewer { top: 2130px; width: 318px; text-align: center; font-size: 17px; color: var(--charcoal); }
  .stars { top: 2157px; width: 318px; text-align: center; color: var(--star); font-size: 14px; letter-spacing: 6px; }

  /* Contact */
  .contact { left: 0; top: 2251px; width: 1200px; height: 409px; background: var(--charcoal); }
  .contact-title { left: 0; width: 1200px; top: 2316px; text-align: center; font-size: 32px; font-weight: 700; color: var(--lime); }
  .field { border: 1px solid var(--lime); color: var(--lime); font-size: 16px; font-weight: 500; padding: 16px 15px; }
  .submit-btn { left: 536px; top: 2561px; width: 128px; height: 38px; background: var(--lime); color: var(--charcoal); font-size: 16px; font-weight: 500; display: flex; align-items: center; justify-content: center; }

  /* Footer */
  .site-footer { left: 0; top: 2695px; width: 1200px; text-align: center; font-size: 12.5px; color: var(--text); }
</style>
</head>
<body>

<header class="abs site-header">
  <nav class="main-nav">
    <a href="#" style="left:104px">Home</a>
    <a href="#" style="left:168px">Advertise</a>
    <a href="#" style="left:256px">Contact</a>
    <a href="#" style="left:358px">Register</a>
  </nav>
  <div class="brand"><span class="brand-dot"></span>KODEO.COM</div>
  <div class="header-search">Search</div>
  <div class="login-btn">Log In</div>
</header>

<section class="abs hero"></section>
<div class="abs hero-visual" role="img" aria-label="Static caravan with a silver SUV and a work van parked in front, each showing a short advert code"></div>

<div class="abs search-panel">
  <svg class="code-arrows" viewBox="0 0 359 110" aria-hidden="true">
    <g fill="none" stroke="#d4ec00" stroke-width="2">
      <polyline points="160,9 164,5 168,9"/><polyline points="223,9 227,5 231,9"/>
      <polyline points="160,100 164,104 168,100"/><polyline points="223,100 227,104 231,100"/>
    </g>
  </svg>
  <div class="code-display">A1</div>
  <div class="category-tabs"><span>car</span><span>caravan</span><span>company</span></div>
  <div class="search-btn">Search</div>
</div>

<svg class="abs feature-swoosh" width="900" height="130" viewBox="0 0 900 130" aria-hidden="true">
  <path d="M5 10 C60 60 160 90 240 80 C300 70 320 50 330 40 L330 60 C310 80 280 100 200 108 C120 110 40 80 5 40 Z" fill="#d4ec00"/>
  <path d="M320 55 L330 30 L400 0 L330 80 Z" fill="#d4ec00"/>
  <path d="M575 0 C600 40 630 70 660 80 L660 100 C620 80 590 50 575 30 Z" fill="#d4ec00"/>
  <path d="M630 95 C700 120 800 110 895 60 L895 35 C810 85 720 100 630 75 Z" fill="#d4ec00"/>
</svg>

<article class="abs feature-card" style="left:160px">
  <svg class="feature-icon" viewBox="0 0 82 82" aria-hidden="true">
    <circle cx="41" cy="41" r="38" fill="#eef7c2"/>
    <g stroke="#333" stroke-width="2" fill="none" stroke-linecap="round">
      <line x1="22" y1="62" x2="46" y2="38"/>
      <line x1="50" y1="22" x2="50" y2="30"/><line x1="46" y1="26" x2="54" y2="26"/>
      <line x1="58" y1="34" x2="62" y2="30"/><line x1="38" y1="26" x2="40" y2="30"/><line x1="56" y1="42" x2="60" y2="44"/>
    </g>
  </svg>
  <h3 class="feature-title">simple</h3>
  <p class="feature-text">create your advert and display your code</p>
</article>
<article class="abs feature-card" style="left:473px">
  <svg class="feature-icon" viewBox="0 0 82 82" aria-hidden="true">
    <circle cx="41" cy="41" r="38" fill="#eef7c2"/>
    <g stroke="#333" stroke-width="1.8" fill="none">
      <circle cx="41" cy="40" r="6"/><circle cx="41" cy="40" r="11"/><circle cx="41" cy="40" r="16"/><circle cx="41" cy="40" r="21"/>
    </g>
  </svg>
  <h3 class="feature-title">unique</h3>
  <p class="feature-text">customers find you by entering your easy-to-remember code</p>
</article>
<article class="abs feature-card" style="left:785px">
  <svg class="feature-icon" viewBox="0 0 82 82" aria-hidden="true">
    <circle cx="41" cy="41" r="38" fill="#eef7c2"/>
    <g stroke="#333" stroke-width="2" fill="none" stroke-linecap="round">
      <circle cx="37" cy="45" r="18"/><circle cx="37" cy="45" r="11"/><circle cx="37" cy="45" r="4"/>
      <line x1="37" y1="45" x2="58" y2="24"/><polyline points="52,22 58,24 60,30"/>
    </g>
  </svg>
  <h3 class="feature-title">effective</h3>
  <p class="feature-text">customers are directed to you and not a list of your competitors</p>
</article>

<section class="abs about"></section>
<div class="abs about-visual" role="img" aria-label="Two businessmen in conversation, shown inside a splash-shaped frame"></div>
<h2 class="abs about-title">About Us</h2>
<div class="abs about-copy">
  <p>Lorem ipsum dolor sit amet, consectetur adipiscing elit, sed do eiusmod tempor incididunt ut labore et dolore magna aliqua. Quis ipsum suspendisse ultrices gravida. Risus commodo viverra maecenas accumsan lacus vel facilisis.</p>
  <p>Sed ut perspiciatis unde omnis iste natus error sit voluptatem accusantium doloremque laudantium, totam rem aperiam, eaque ipsa quae ab illo inventore veritatis et quasi architecto beatae vitae dicta sunt explicabo. Nemo enim ipsam voluptatem quia voluptas sit aspernatur aut odit aut fugit, sed quia consequuntur magni dolores eos qui ratione voluptatem sequi nesciunt. Neque porro quisquam est, qui dolorem ipsum quia dolor sit amet.</p>
</div>

<h2 class="abs testimonials-title">Testimonials</h2>

<article class="abs testimonial" style="left:91px">
  <div class="avatar" role="img" aria-label="Customer portrait"></div>
  <p>Lorem ipsum dolor sit amet, consectetur adipiscing elit, sed do eiusmod tempor incididunt ut labore et dolore magna aliqua. Ut enim ad minim veniam, quis nostrud exercitation ullamco laboris nisi ut aliquip consequat.</p>
  <svg class="pointer" width="38" height="36" viewBox="0 0 38 36" aria-hidden="true"><path d="M0 0 L19 34 L38 0" fill="#fff" stroke="#c9c9c9"/></svg>
</article>
<article class="abs testimonial is-featured" style="left:441px">
  <div class="avatar" role="img" aria-label="Customer portrait"></div>
  <p>Lorem ipsum dolor sit amet, consectetur adipiscing elit, sed do eiusmod tempor incididunt ut labore et dolore magna aliqua. Ut enim ad minim veniam, quis nostrud exercitation ullamco laboris nisi ut aliquip consequat.</p>
  <svg class="pointer" width="38" height="36" viewBox="0 0 38 36" aria-hidden="true"><path d="M0 0 L19 34 L38 0" fill="#fff" stroke="#d4ec00"/></svg>
</article>
<article class="abs testimonial" style="left:791px">
  <div class="avatar" role="img" aria-label="Customer portrait"></div>
  <p>Lorem ipsum dolor sit amet, consectetur adipiscing elit, sed do eiusmod tempor incididunt ut labore et dolore magna aliqua. Ut enim ad minim veniam, quis nostrud exercitation ullamco laboris nisi ut aliquip consequat.</p>
  <svg class="pointer" width="38" height="36" viewBox="0 0 38 36" aria-hidden="true"><path d="M0 0 L19 34 L38 0" fill="#fff" stroke="#c9c9c9"/></svg>
</article>

<div class="abs reviewer" style="left:91px">Tom Hale</div>
<div class="abs reviewer" style="left:441px">Tom Hale</div>
<div class="abs reviewer" style="left:791px">Tom Hale</div>
<div class="abs stars" style="left:91px">★★★★★</div>
<div class="abs stars" style="left:441px">★★★★★</div>
<div class="abs stars" style="left:791px">★★★★★</div>

<section class="abs contact"></section>
<h2 class="abs contact-title">Contact Us</h2>
<div class="abs field" style="left:124px;top:2394px;width:464px;height:58px">Name</div>
<div class="abs field" style="left:124px;top:2474px;width:464px;height:58px">Email</div>
<div class="abs field" style="left:612px;top:2395px;width:464px;height:137px">Message</div>
<div class="abs submit-btn">Submit</div>

<footer class="abs site-footer">© Copyrights 2023 kodeo | All Rights Reserved</footer>

</body>
</html>
```